I need a business card designed using the logo provided either vertical or horizontal......Harbourline Property Group is an Australian based real estate company that caters for the upper end of the market so the design of the business card "must reflect" the companies image!!
Colour combinations are optional but "must be realistic" and must be able to be accurately useable CMYK colours.
Please consider that any colours used "must be able to be used" and be suitable in following designs for "pull out banner signs" and "real estate signs".
The colours and the font in the attached designs are for example and other combinations are encouraged.
Target Market(s)
The High End of the Australian real estate market
Industry/Entity Type
Business
Contact Information for Business Card
Logo - Business Name - Director + Licensed Real Estate Agent - Mobile Number (Cell Phone) - Business Number - Fax - Email Address - Web address
Requirements
Must have
- Designs and colours (CMYK) that can easily be interpreted by an Australian printer.
Nice to have
- Some alternative ideas on colour and font..........the ones provided are ok and have been provided as an example but I am looking for alternative ideas
Should not have
- Loud, overly bright colours. Designs that do not reflect the professional standards of the business.
- Designs that look good on a computer monitor but can not be re-created on a printing press.............this is most important when it comes to shading etc.

```html
<!DOCTYPE html>
<html lang="en">
<head>
<meta charset="utf-8">
<title>Harbourline Property Group – Business Card</title>
<link href="https://fonts.googleapis.com/css2?family=Open+Sans:wght@400;600;700&display=swap" rel="stylesheet">
<style>
  :root {
    --gold: #b27b2a;
    --ink: #231f20;
    --white: #ffffff;
    --brand-grey: #5c5c5e;
    --brand-light: #e6e6e6;
    --backdrop: #d9d9d9;
    --card-w: 620px;
    --card-h: 354px;
  }
  * { box-sizing: border-box; margin: 0; padding: 0; }
  html, body {
    width: 1200px; height: 900px; overflow: hidden;
    background: var(--backdrop);
    font-family: "Open Sans", Arial, sans-serif;
  }
  .canvas {
    width: 1200px; height: 900px;
    display: flex; flex-direction: column;
    align-items: center; justify-content: center; gap: 60px;
  }
  .card {
    position: relative;
    width: var(--card-w); height: var(--card-h);
    overflow: hidden;
    box-shadow: 0 6px 18px rgba(0,0,0,0.18);
  }

  /* Back face */
  .card--back { background: var(--ink); }
  .card--back .band { position: absolute; left: 0; right: 0; background: var(--gold); }
  .card--back .band--top { top: 0; height: 56px; }
  .card--back .band--bottom { bottom: 0; height: 64px; }
  .card--back .brand {
    position: absolute; left: 0; right: 0; top: 56px; bottom: 64px;
    display: flex; align-items: center; justify-content: center; gap: 14px;
  }
  .brand__mark { width: 22px; height: 22px; border-radius: 50%; }
  .brand__name {
    font-weight: 600; letter-spacing: 3px; text-transform: uppercase;
    font-size: 22px; line-height: 1;
  }
  .card--back .brand__mark { background: var(--brand-grey); }
  .card--back .brand__name { color: var(--brand-grey); }

  /* Front face */
  .card--front { background: var(--gold); }
  .card--front .header {
    position: absolute; left: 0; top: 0; width: 100%; height: 150px;
    background: var(--ink);
  }
  .card--front .footer-strip {
    position: absolute; left: 0; bottom: 0; width: 100%; height: 22px;
    background: var(--ink);
  }
  .card--front .brand {
    position: absolute; right: 28px; top: 88px;
    display: flex; align-items: center; gap: 12px;
  }
  .card--front .brand__mark { background: var(--gold); width: 20px; height: 20px; }
  .card--front .brand__name { color: var(--brand-light); font-size: 19px; letter-spacing: 2.5px; }

  .person { position: absolute; left: 26px; top: 160px; color: var(--white); }
  .person__name { font-size: 22px; font-weight: 700; line-height: 1.1; }
  .person__title { font-size: 13px; font-weight: 400; margin-top: 3px; }

  .contact {
    position: absolute; right: 24px; top: 210px;
    list-style: none; color: var(--white);
    font-size: 15px; line-height: 22px; text-align: right;
  }
  .contact__item { display: flex; align-items: center; justify-content: flex-end; gap: 10px; white-space: nowrap; }
  .contact__icon { width: 14px; height: 14px; fill: var(--white); flex: none; }
</style>
</head>
<body>
<main class="canvas">

  <section class="card card--back" aria-label="Business card back">
    <div class="band band--top"></div>
    <div class="brand">
      <span class="brand__mark"></span>
      <span class="brand__name">Harbourline Property Group</span>
    </div>
    <div class="band band--bottom"></div>
  </section>

  <section class="card card--front" aria-label="Business card front">
    <div class="header"></div>
    <div class="brand">
      <span class="brand__mark"></span>
      <span class="brand__name">Harbourline Property Group</span>
    </div>

    <div class="person">
      <p class="person__name">Daniel Whitford</p>
      <p class="person__title">Managing Director</p>
    </div>

    <ul class="contact">
      <li class="contact__item">0412 555 018
        <svg class="contact__icon" viewBox="0 0 16 16"><path d="M2 6c0-2 2-3 6-3s6 1 6 3l-3 1-1-2H6L5 7 2 6zm2 2h8l1 5H3l1-5zm4 1.5a1.5 1.5 0 1 0 0 3 1.5 1.5 0 0 0 0-3z"/></svg>
      </li>
      <li class="contact__item">(02) 9555 0147
        <svg class="contact__icon" viewBox="0 0 16 16"><path d="M4 1h6l2 2v3H4V1zm-2 6h12v6h-2v2H4v-2H2V7zm3 4v3h6v-3H5z"/></svg>
      </li>
      <li class="contact__item">hello@harbourlinepg.com.au
        <svg class="contact__icon" viewBox="0 0 16 16"><path d="M1 3h14v10H1V3zm1.5 1.2L8 8.5l5.5-4.3H2.5z"/></svg>
      </li>
      <li class="contact__item">www.harbourlinepg.com.au
        <svg class="contact__icon" viewBox="0 0 16 16"><path d="M6.5 9.5l3-3 1 1-3 3-1-1zM3 11l3-3 1 1-3 3 1 1 3-3 1 1-3 3a1.5 1.5 0 0 1-2 0l-1-1a1.5 1.5 0 0 1 0-2zm10-6l-3 3-1-1 3-3-1-1-3 3-1-1 3-3a1.5 1.5 0 0 1 2 0l1 1a1.5 1.5 0 0 1 0 2z"/></svg>
      </li>
      <li class="contact__item">27 Wharf Street, Sydney NSW, Australia 2000
        <svg class="contact__icon" viewBox="0 0 16 16"><path d="M8 1a5 5 0 0 1 5 5c0 4-5 9-5 9S3 10 3 6a5 5 0 0 1 5-5zm0 3a2 2 0 1 0 0 4 2 2 0 0 0 0-4z"/></svg>
      </li>
    </ul>

    <div class="footer-strip"></div>
  </section>

</main>
</body>
</html>
```